Letterhead and matching envelope design for a dental office

We need a new stationary design, letterhead and envelope #10, for a dental office in Denver area. We are called Bright Harbor Dental. We want a simple and minimalistic design but not a boring design. I wish to have one good point that makes it look professional. I have attached our logo. Feel free to use either one. I want the design for letterhead and envelope look like a "matching pair" but not look the same. The envelope doesn't have to be white and it will have an address window on bottom left.

Target Market(s)

everyone who visits dentist (adults)

Industry/Entity Type

Dental

Font styles to use
Other font styles liked:
• close to font on logo or something that matches well

Requirements
Must have
• professional
• simple, minimalistic
• unique point that stands out
Nice to have
• matching but not same design for letterhead and envelope
Should not have
• not look like all the other boring designs
• no flowery, distracting feats

```html
<!DOCTYPE html>
<html lang="en">
<head>
<meta charset="utf-8">
<title>Bright Harbor Dental — Letterhead</title>
<link rel="stylesheet" href="https://fonts.googleapis.com/css2?family=Cinzel:wght@600&family=PT+Sans:wght@400;700&display=swap">
<style>
  :root {
    --backdrop: #a9d3c6;
    --paper: #ffffff;
    --paper-tint: #f1f4f3;
    --swoosh: #e3e6e5;
    --swoosh-deep: #d4d8d7;
    --brand-green: #1e9a3c;
    --brand-green-dark: #17802f;
    --leaf-tint: #e6efe6;
    --ink: #3a3d3c;
    --ink-soft: #6b706e;
    --rule-grey: #a9acab;
  }
  * { box-sizing: border-box; margin: 0; padding: 0; }
  html, body {
    width: 1200px; height: 784px; overflow: hidden;
    background: var(--backdrop);
  }
  .canvas {
    position: relative; width: 1200px; height: 784px;
    display: flex; align-items: center; justify-content: center;
  }
  .letterhead {
    position: relative; width: 510px; height: 722px;
    background: var(--paper); overflow: hidden;
    box-shadow: 0 2px 10px rgba(40, 80, 70, .18);
  }
  .letterhead__swooshes { position: absolute; inset: 0; width: 100%; height: 100%; }
  .letterhead__leaf {
    position: absolute; left: 150px; top: 505px; width: 120px; height: 70px;
    background: radial-gradient(ellipse at 45% 50%, var(--leaf-tint) 0%, rgba(230,239,230,0) 72%);
  }
  .brand-mark {
    position: absolute; top: 40px; right: 36px;
    display: flex; align-items: center; gap: 8px;
  }
  .brand-mark__dot {
    width: 12px; height: 12px; border-radius: 50%; background: var(--brand-green);
  }
  .brand-mark__name {
    font-family: "Cinzel", serif; font-weight: 600; font-size: 14px;
    letter-spacing: .14em; color: var(--brand-green);
  }
  .contact {
    position: absolute; left: 34px; bottom: 70px;
    font-family: "PT Sans", sans-serif; color: var(--ink);
  }
  .contact__name {
    font-family: "Cinzel", serif; font-weight: 600; font-size: 13px;
    letter-spacing: .12em; color: var(--brand-green); margin-bottom: 6px;
  }
  .contact__line {
    display: flex; align-items: center; gap: 5px;
    font-size: 8.5px; color: var(--ink-soft); line-height: 1.6;
  }
  .contact__icon {
    width: 9px; height: 9px; border-radius: 50%; background: var(--brand-green);
    display: inline-flex; align-items: center; justify-content: center;
  }
  .contact__icon svg { width: 6px; height: 6px; }
  .contact__legal { font-size: 8.5px; font-weight: 700; color: var(--ink); margin-top: 2px; }
  .footer-band {
    position: absolute; left: 0; right: 0; bottom: 0; height: 12px;
    display: flex;
  }
  .footer-band__green {
    flex: 1; background: linear-gradient(180deg, var(--brand-green) 0%, var(--brand-green-dark) 100%);
    clip-path: polygon(0 0, 100% 0, 100% 100%, 0 100%);
  }
  .footer-band__grey {
    width: 70px; background: linear-gradient(180deg, #c7caca 0%, var(--rule-grey) 100%);
  }
</style>
</head>
<body>
<main class="canvas">
  <article class="letterhead">
    <svg class="letterhead__swooshes" viewBox="0 0 510 722" preserveAspectRatio="none" aria-hidden="true">
      <path d="M0 0 H120 C60 200 40 380 0 520 Z" fill="var(--paper-tint)"/>
      <path d="M510 560 C380 600 300 660 270 722 H510 Z" fill="var(--paper-tint)"/>
      <path d="M60 0 C120 180 110 360 30 560" stroke="var(--swoosh)" stroke-width="10" fill="none"/>
      <path d="M95 0 C150 200 140 400 70 600" stroke="var(--swoosh)" stroke-width="4" fill="none"/>
      <path d="M510 470 C420 560 360 620 330 722" stroke="var(--swoosh-deep)" stroke-width="8" fill="none"/>
      <path d="M510 440 C400 540 330 620 300 722" stroke="var(--swoosh)" stroke-width="3" fill="none"/>
    </svg>

    <div class="letterhead__leaf" role="img" aria-label="Faint leaf decoration"></div>

    <div class="brand-mark">
      <span class="brand-mark__dot"></span>
      <span class="brand-mark__name">Bright Harbor Dental</span>
    </div>

    <address class="contact">
      <p class="contact__name">Bright Harbor Dental</p>
      <p class="contact__line">
        <span class="contact__icon"><svg viewBox="0 0 10 10"><path d="M5 1a3 3 0 0 1 3 3c0 2.2-3 5-3 5S2 6.2 2 4a3 3 0 0 1 3-3z" fill="#fff"/></svg></span>
        Suite 6, 62 Harbor Street, Denver CO 80202
      </p>
      <p class="contact__line">
        <span class="contact__icon"><svg viewBox="0 0 10 10"><path d="M2 1h2l1 2-1 1c.5 1 1 1.5 2 2l1-1 2 1v2c-4 0-7-3-7-7z" fill="#fff"/></svg></span>
        303 555 0142
        <span class="contact__icon"><svg viewBox="0 0 10 10"><rect x="2" y="2" width="6" height="6" fill="#fff"/></svg></span>
        303 555 0143
        <span class="contact__icon"><svg viewBox="0 0 10 10"><rect x="3" y="1" width="4" height="8" rx="1" fill="#fff"/></svg></span>
        303 555 0188
      </p>
      <p class="contact__legal">Provider No. 418205B &nbsp;|&nbsp; Tax ID 84 213 907 561</p>
    </address>

    <div class="footer-band">
      <span class="footer-band__green"></span>
      <span class="footer-band__grey"></span>
    </div>
  </article>
</main>
</body>
</html>
```